Halvick Ledgers & Advisory Tri-Fold Brochure (8.5"x11")

I need a professional looking brochure for my bookkeeping business. I am looking for something professional yet casual (not too corporate looking). I have attached a sample brochure that will outline the areas and a copy of our logo. I'd like to stick with shades of blue. The final product should communicate professional and personal.

Target Market(s)

Small service businesses.

Industry/Entity Type

Business

Font styles to use
Sans Serif

Requirements
Must have
• Professional looking photos of people in areas where it asks for a picture.

```html
<!DOCTYPE html>
<html lang="en">
<head>
<meta charset="utf-8">
<title>Halvick Ledgers &amp; Advisory – Services Brochure</title>
<link rel="stylesheet" href="https://fonts.googleapis.com/css2?family=Source+Sans+3:wght@400;600;700&display=swap">
<style>
  :root {
    --bg-edge: #b9dff5;
    --bg-mid: #eef8fd;
    --heading-blue: #1b78bd;
    --accent-cyan: #1aa9e2;
    --deep-navy: #0d4d8c;
    --body-text: #4a4d52;
    --rule-blue: #2b8ad0;
  }
  * { box-sizing: border-box; margin: 0; padding: 0; }
  html, body { width: 1200px; height: 927px; overflow: hidden; }
  body {
    font-family: "Source Sans 3", sans-serif;
    color: var(--body-text);
    background: radial-gradient(ellipse 75% 95% at 50% 45%, var(--bg-mid) 0%, #dff1fb 50%, var(--bg-edge) 100%);
    position: relative;
  }
  .globe-art {
    position: absolute; left: -42px; top: -46px; width: 170px; height: 170px; border-radius: 50%;
    background: radial-gradient(circle at 40% 40%, #f4f8fb 0%, #cdd9e2 60%, #aebfcc 100%);
    opacity: .75;
  }
  .block { position: absolute; }
  .section-title {
    font-weight: 400; color: var(--heading-blue); font-size: 27px; line-height: 32.5px; text-align: center;
  }
  .main-title {
    font-weight: 600; color: var(--heading-blue); font-size: 37px; line-height: 36px; text-align: center; letter-spacing: .5px;
  }
  .copy {
    font-size: 17.2px; line-height: 21.3px; text-align: justify; text-align-last: left;
  }
  .rule { position: absolute; height: 1.6px; background: var(--rule-blue); }
  .col-left { left: 33px; width: 336px; }
  .col-mid { left: 424px; width: 342px; }
  .col-right { left: 841px; width: 326px; }
  .service-list { list-style: none; font-size: 17.2px; line-height: 21.3px; }
  .why-title { font-weight: 600; color: var(--heading-blue); font-size: 37px; line-height: 46px; text-align: center; }
  .benefits { list-style: none; text-align: center; color: var(--accent-cyan); font-weight: 600; font-size: 29px; line-height: 33.3px; }
  .heartbeat { font-weight: 600; color: var(--deep-navy); font-size: 27px; line-height: 32.5px; text-align: center; }
  .process { font-size: 17.2px; line-height: 24px; text-align: justify; text-align-last: left; }
</style>
</head>
<body>
  <div class="globe-art" role="img" aria-label="Faint illustration of a globe"></div>

  <!-- Left panel: services -->
  <h1 class="block main-title col-left" style="top:115px;">SERVICES</h1>
  <h2 class="block section-title col-left" style="top:181px;">Full Charge Bookkeeping</h2>
  <p class="block copy col-left" style="top:234px;">We can manage all aspects of your bookkeeping and business financials and communicate to you as much and as often as you want.</p>
  <div class="rule" style="left:94px; width:217px; top:345px;"></div>
  <h2 class="block section-title col-left" style="top:352px;">Cash Management<br>(Bill Pay &amp; Invoicing)<br>&amp; Vendor Management</h2>
  <p class="block copy col-left" style="top:487px;">We can handle every step from receiving bills, communicating with vendor and paying bills. We take a lot pride in helping our clients save money and one way is negotiating with vendors and finding appropriate discounts.</p>
  <div class="rule" style="left:94px; width:217px; top:624px;"></div>
  <h2 class="block section-title col-left" style="top:632px;">Financial Statements</h2>
  <p class="block copy col-left" style="top:686px;">Profit and Loss – Balance Sheet – Statement of Cash Flow – Industry Specific<br>We accurately prepare monthly, quarterly &amp; annual financial statements in a timely manner. We also take the time to review these statements with you so that you understand the financial health of your business.</p>

  <!-- Middle panel -->
  <h2 class="block section-title col-mid" style="top:29px;">Account Reconciliations</h2>
  <p class="block copy col-mid" style="top:83px;">From bank account to credit card statements to vendor statements. We reconcile all of your accounts that impact your finances.</p>
  <div class="rule" style="left:488px; width:230px; top:185px;"></div>
  <h2 class="block section-title col-mid" style="top:199px;">Professional liaison</h2>
  <p class="block copy col-mid" style="top:262px;">We will work directly with your other business partners – Bankers, CPA, Insurance, Payroll, Attorney… Need a loan? We will work directly with your banker to make the process as simple as possible. Does your CPA need some data? Let us take care of that while you continue making your customers happy.</p>
  <div class="rule" style="left:488px; width:230px; top:444px;"></div>
  <h2 class="block section-title col-mid" style="top:458px;">Business Services</h2>
  <ul class="block service-list" style="left:477px; top:522px;">
    <li>Budget</li>
    <li>Create Proper Financial Systems</li>
    <li>Projections</li>
    <li>Customized Reporting</li>
    <li>Protection Planning</li>
    <li>Benchmarking</li>
    <li>Online Filing Cabinet (Paperless)</li>
  </ul>
  <div class="rule" style="left:488px; width:230px; top:691px;"></div>
  <h2 class="block section-title col-mid" style="top:701px;">Exit/Succession Planning</h2>
  <p class="block copy col-mid" style="top:758px;">We help you prepare your business for the next transition – planned (retirement) or unplanned (health). You’ve sacrificed to build this business (asset) we can help you transition it in the most efficient and valuable way.</p>

  <!-- Right panel -->
  <h1 class="block why-title" style="left:826px; width:341px; top:18px;">Why Outsource<br>Bookkeeping?</h1>
  <ul class="block benefits" style="left:826px; width:341px; top:131px;">
    <li>Save Time</li>
    <li>Save Money</li>
    <li>Expertise</li>
    <li>Focused Staff</li>
    <li>Technology</li>
    <li>Experience</li>
  </ul>
  <div class="rule" style="left:886px; width:228px; top:336px;"></div>
  <p class="block heartbeat" style="left:826px; width:341px; top:353px;">The Financial Numbers<br>are the Heart Beat of an<br>organization</p>
  <div class="block process col-right" style="top:476px;">
    <p>The Process</p>
    <p style="margin-top:21px;">Contact Us – we like to hear from you No-Obligation Consultation</p>
    <p style="margin-top:24px;">Review Current Process – identify strengths and weaknesses</p>
    <p style="margin-top:24px;">Recommend and implement new bookkeeping process</p>
    <p style="margin-top:22px;">Ongoing bookkeeping partnership</p>
    <p style="margin-top:23px;">Provide your company with more value and service to keep earning your business (ongoing)</p>
  </div>
</body>
</html>
```